Modern Homepage Design for brenvik.nl – Fish & Chicken Food Webshop

Brenvik.nl is an online store that sells fish and chicken food. The design should be visually appealing, easy to navigate, and optimized for e-commerce. We want a layout that helps customers quickly find what they need and encourages them to explore our products.
A good example of the style and structure we like is dierkamp.nl – clean layout, clear product focus, and user-friendly navigation.
Brand Colors (must be used):
Orange: #f7a441
Dark Gray: #3c3c3b
White: #ffffff
Please use these colors consistently throughout the design.
Homepage Requirements:
The homepage should include the following sections:
Main Slider / Hero Banner
A large, eye-catching slider at the top of the page to highlight promotions or featured categories.
Category Blocks
A section with clear, clickable blocks or tiles that link to main product categories (e.g., Fish Food, Chicken Food, Accessories).
Featured Products
A section showcasing selected or best-selling products.
Special Offers / Promotions
A space to highlight current deals or limited-time offers.
Three Banners in a Row
A section with three horizontal banners side by side, which can be used for promotions, shipping info, or other key messages.
Unique Selling Points (USPs)
A section that briefly explains what makes our store different (e.g., fast delivery, high-quality feed, trusted by professionals).
SEO Content Block
A short paragraph of text for SEO purposes (use Lorem Ipsum for dummy content).
Footer Design
Include space for contact information, navigation links, and social media.
Design Notes:
The design must be responsive and mobile-friendly.
Focus on clean layout, good spacing, and easy navigation.
Use modern fonts and a clear visual hierarchy.
We are only looking for the homepage design at this stage, but we may work with the selected designer on additional pages later.
Deliverables:
Homepage design in layered PSD, Figma, or Adobe XD format
Any fonts and assets used
Preview images/mockups
We look forward to seeing your ideas and working with a designer who can bring our brand to life with a fresh and functional homepage design.
Let us know if you have any questions.
Hobby Animal Keepers, Pet Owners
Animal Nutrition & Feed
2 page

```html
<!DOCTYPE html>
<html lang="en">
<head>
<meta charset="utf-8">
<title>Brenvik – Fish & Chicken Food Webshop</title>
<link href="https://fonts.googleapis.com/css2?family=Lexend:wght@400;500;600&family=Lato:wght@400;700&display=swap" rel="stylesheet">
<style>
:root{
  --orange:#f7a441;
  --dark:#3c3c3b;
  --white:#ffffff;
  --ink:#222222;
  --muted:#777777;
  --soft:#f5f5f5;
  --line:#d9d9d9;
}
*{box-sizing:border-box;margin:0;padding:0}
html,body{width:1200px;height:3375px;overflow:hidden}
body{font-family:'Lato',sans-serif;color:var(--ink);background:var(--white);position:relative}
.head{font-family:'Lexend',sans-serif}
a{color:inherit;text-decoration:none}

.topbar{height:43px;display:flex;align-items:center;justify-content:space-between;padding:0 368px 0 112px;font-size:14px}
.topbar .item{display:flex;align-items:center;gap:9px}
.topbar .contacts{display:flex;gap:26px;align-items:center}
.topbar .sep{color:var(--line)}

.header{height:94px;background:var(--dark);display:flex;align-items:center;padding:0 112px;justify-content:space-between}
.brand{display:flex;align-items:center;gap:8px;font-family:'Lexend',sans-serif;font-weight:600;font-size:44px;color:var(--white)}
.brand .dot{width:36px;height:36px;border-radius:50%;background:var(--orange)}
.search{width:468px;height:50px;border-radius:25px;background:var(--white);display:flex;align-items:center;justify-content:space-between;padding:0 24px 0 32px;font-size:14px;color:#444}
.cart{height:50px;border-radius:25px;background:var(--orange);display:flex;align-items:center;gap:8px;padding:0 22px;font-size:14px;font-weight:700;color:var(--dark)}

.nav{height:77px;display:flex;align-items:center;justify-content:center;gap:32px;font-family:'Lexend',sans-serif;font-size:19px;color:#333}
.nav .bar{color:#333}

.hero{height:514px;position:relative}
.hero-main{position:absolute;left:0;top:0;width:811px;height:514px;background:linear-gradient(180deg,#8fb6de 0%,#c9d6b8 45%,#e6b664 62%,#6f8a2c 78%,#4d6a1e 100%)}
.hero-side1{position:absolute;left:819px;top:0;width:381px;height:240px;background:linear-gradient(135deg,#5a3314,#b96a2c 60%,#d08a44)}
.hero-side2{position:absolute;left:819px;top:248px;width:381px;height:266px;background:linear-gradient(135deg,#f3f3f1,#e9e4dc)}
.hero-copy{position:absolute;left:112px;top:98px;width:380px}
.hero-copy h1{font-family:'Lexend',sans-serif;font-weight:600;font-size:44px;line-height:51px;color:#111}
.hero-copy p{margin-top:20px;font-size:17px;line-height:30px;color:#1a1a1a}
.btn-light{display:inline-block;margin-top:18px;background:var(--white);border-radius:26px;padding:14px 21px;font-family:'Lexend',sans-serif;font-weight:600;font-size:15px;color:#111}

.about{position:relative;height:626px}
.about-ring{position:absolute;left:112px;top:98px;width:438px;height:450px;border-radius:50%;background:var(--orange)}
.about-photo{position:absolute;left:120px;top:116px;width:392px;height:392px;border-radius:50%;background:radial-gradient(circle at 50% 45%,#d9cfc2,#9a8570 55%,#4a3a2c)}
.about-text{position:absolute;left:598px;top:90px;width:490px}
.about-text h2{font-family:'Lexend',sans-serif;font-weight:400;font-size:44px;color:#222}
.about-text h3{margin-top:14px;font-family:'Lexend',sans-serif;font-weight:400;font-size:24px;line-height:38px;color:var(--orange)}
.about-text p{margin-top:10px;font-size:14.5px;line-height:26px;color:#222}
.about-text p+p{margin-top:26px}
.btn-dark{display:inline-flex;align-items:center;gap:12px;margin-top:26px;background:var(--dark);border-radius:26px;padding:9px 18px 9px 12px;color:var(--orange);font-family:'Lexend',sans-serif;font-size:15px}
.btn-dark .dot{width:30px;height:30px;border-radius:50%;border:4px solid var(--orange)}

.slogan{position:relative;height:60px;margin:0 112px}
.slogan:before{content:"";position:absolute;left:0;right:0;top:27px;border-top:1px solid var(--line)}
.slogan span{position:relative;display:block;width:600px;margin:0 auto;text-align:center;background:var(--white);font-family:'Lexend',sans-serif;font-size:25px;color:#333}

.usps{display:flex;justify-content:space-between;padding:0 112px;margin-top:48px;height:140px}
.usp{display:flex;gap:14px;align-items:flex-start}
.usp .ico{width:50px;height:50px;border-radius:50%;background:var(--dark);display:flex;align-items:center;justify-content:center}
.usp .ico.alt{background:var(--orange)}
.usp h4{font-family:'Lexend',sans-serif;font-weight:400;font-size:17px;color:#333;margin-top:3px}
.usp p{font-size:12.5px;color:#555;margin-top:6px}

.section-title{text-align:center;font-family:'Lexend',sans-serif;font-weight:400;font-size:46px;color:#333}
.cats{position:relative;height:300px}
.cats .section-title{padding-top:0}
.cat-row{position:absolute;top:97px;left:112px;display:flex;gap:15px}
.cat{width:184px;text-align:center}
.cat .tile{height:108px;border-radius:22px}
.cat span{display:block;margin-top:10px;font-family:'Lexend',sans-serif;font-size:17px;color:#111}
.arrow{position:absolute;top:133px}

.deals{height:430px}
.deal-row{display:flex;justify-content:space-between;padding:0 45px 0 38px;margin-top:28px}
.deal{position:relative;width:348px;height:188px;border-radius:12px;overflow:hidden}
.deal .shape{position:absolute;left:0;top:25px;width:190px;height:163px;background:var(--orange);border-radius:0 110px 0 0}
.deal .txt{position:absolute;left:14px;top:52px;font-family:'Lexend',sans-serif;font-size:20px;line-height:29px;color:#222}
.deal .txt u{display:block;font-size:15px;margin-top:6px}

.featured{background:var(--soft);height:610px;padding-top:50px}
.prod-row{display:flex;gap:26px;padding:0 112px;margin-top:36px}
.prod{width:308px;height:386px;border:1.5px dashed var(--orange);border-radius:14px;padding:17px 18px}
.prod .img{height:193px;border-radius:10px}
.prod h5{margin-top:22px;font-family:'Lexend',sans-serif;font-weight:500;font-size:15px;line-height:26px;color:#111}
.prod p{margin-top:8px;font-size:12.5px;line-height:26px;color:#777}
.prod a{display:block;margin-top:6px;font-size:12.5px;color:var(--orange);text-decoration:underline}

.footer{background:var(--dark);height:425px;position:relative;color:var(--white)}
.footer .brand{position:absolute;left:116px;top:70px;font-size:56px}
.footer .brand .dot{width:46px;height:46px}
.fcol{position:absolute;top:94px}
.fcol h6{font-family:'Lexend',sans-serif;font-weight:500;font-size:21px}
.fcol ul{list-style:none;margin-top:14px}
.fcol li{font-size:15px;line-height:34px;display:flex;align-items:center;gap:10px}
.fcontact{display:flex;gap:12px;align-items:flex-start;font-size:15px;line-height:27px;margin-top:16px}
.fcontact .ic{width:32px;height:32px;border-radius:50%;background:var(--white);display:flex;align-items:center;justify-content:center;flex:none}
.footer .rule{position:absolute;left:112px;right:112px;top:335px;border-top:1px solid #8a8a8a}
.footer .copy{position:absolute;top:370px;width:100%;text-align:center;font-size:15px;font-weight:700}
</style>
</head>
<body>

<div class="topbar">
  <div class="item">
    <svg width="30" height="20" viewBox="0 0 30 20"><rect x="1" y="3" width="17" height="12" rx="2" fill="#f7a441"/><path d="M18 7h6l4 4v4H18z" fill="#f7a441"/><circle cx="7" cy="17" r="2.5" fill="#3c3c3b"/><circle cx="23" cy="17" r="2.5" fill="#3c3c3b"/></svg>
    <span>Free shipping from €19</span>
  </div>
  <div class="contacts">
    <div class="item"><svg width="16" height="16" viewBox="0 0 24 24"><path d="M6.6 10.8a15 15 0 006.6 6.6l2.2-2.2a1 1 0 011-.25 11.4 11.4 0 003.6.57 1 1 0 011 1V20a1 1 0 01-1 1A17 17 0 013 4a1 1 0 011-1h3.5a1 1 0 011 1c0 1.25.2 2.45.57 3.6a1 1 0 01-.25 1z" fill="#f7a441"/></svg><span>0612 480 917</span></div>
    <span class="sep">|</span>
    <div class="item"><svg width="18" height="14" viewBox="0 0 18 14"><rect width="18" height="14" rx="2" fill="#f7a441"/><path d="M1 2l8 6 8-6" stroke="#fff" stroke-width="1.6" fill="none"/></svg><span>info@brenvik.nl</span></div>
  </div>
</div>

<header class="header">
  <div class="brand"><span class="dot"></span>brenvik</div>
  <div class="search"><span>Searching For......</span>
    <svg width="14" height="14" viewBox="0 0 14 14"><circle cx="6" cy="6" r="4.5" stroke="#333" stroke-width="1.6" fill="none"/><path d="M9.5 9.5L13 13" stroke="#333" stroke-width="1.6"/></svg></div>
  <div class="cart"><svg width="22" height="20" viewBox="0 0 22 20"><path d="M1 2h3l3 11h11l3-8H6" stroke="#111" stroke-width="2" fill="none"/><circle cx="8" cy="17" r="1.8" fill="#111"/><circle cx="17" cy="17" r="1.8" fill="#111"/><path d="M6 5h15l-3 8H8z" fill="#111"/></svg>Shopping Cart</div>
</header>

<nav class="nav">
  <a>Home</a><span class="bar">|</span><a>Fish Food</a><span class="bar">|</span><a>Chicken Food</a><span class="bar">|</span><a>Accessories</a><span class="bar">|</span><a>Offers</a><span class="bar">|</span><a>About Us</a><span class="bar">|</span><a>Contact Us</a>
</nav>

<section class="hero">
  <div class="hero-main" role="img" aria-label="Cows grazing in a green meadow at sunset"></div>
  <div class="hero-side1" role="img" aria-label="Dog sitting beside a bag of feed and a bowl in a kitchen"></div>
  <div class="hero-side2" role="img" aria-label="Bowls of pet food and treats arranged on a white surface"></div>
  <div class="hero-copy">
    <h1>Premium Feed for Healthy Animals</h1>
    <p>Fast, reliable delivery straight to your door. Our specialists are ready to guide you.</p>
    <a class="btn-light">Get Yours Today</a>
  </div>
</section>

<section class="about">
  <div class="about-ring"></div>
  <div class="about-photo" role="img" aria-label="Group of farm animals crowding together in a barn"></div>
  <div class="about-text">
    <h2>About Brenvik</h2>
    <h3>Quality Feed. Trusted Service. Healthier Animals.</h3>
    <p>At Brenvik, we believe that every fish and chicken deserves the best nutrition possible. For decades, we've been supplying premium fish food, chicken feed, and animal care products to hobbyists, breeders, and small farms across the Netherlands.</p>
    <p>What started as a small local business has grown into a trusted online store for quality animal feed, known for our commitment to freshness, fast delivery, and honest advice. We carefully select every product we offer — partnering with reliable brands and feed specialists who share our passion for animal health and sustainability.</p>
    <a class="btn-dark"><span class="dot"></span>Read More</a>
  </div>
</section>

<div class="slogan"><span>Everything for my pet. My number one choice.</span></div>

<section class="usps">
  <div class="usp"><div class="ico"><svg width="26" height="18" viewBox="0 0 30 20"><rect x="1" y="3" width="17" height="12" rx="2" fill="#f7a441"/><path d="M18 7h6l4 4v4H18z" fill="#f7a441"/><circle cx="7" cy="17" r="2.5" fill="#fff"/><circle cx="23" cy="17" r="2.5" fill="#fff"/></svg></div>
    <div><h4>Fast Delivery</h4><p>Lorem ipsum dolor sit amet</p></div></div>
  <div class="usp"><div class="ico alt"><svg width="22" height="22" viewBox="0 0 22 22"><rect x="3" y="8" width="16" height="12" rx="2" fill="#3c3c3b"/><path d="M7 8V5a4 4 0 018 0v3" stroke="#3c3c3b" stroke-width="2" fill="none"/></svg></div>
    <div><h4>High-quality Feed</h4><p>Lorem ipsum dolor sit amet</p></div></div>
  <div class="usp"><div class="ico"><svg width="24" height="22" viewBox="0 0 24 22"><path d="M2 12l5-4 5 3 5-3 5 4-8 7h-4z" fill="#f7a441"/><path d="M8 5l3 3 5-6" stroke="#fff" stroke-width="2" fill="none"/></svg></div>
    <div><h4>Trusted by Professionals</h4><p>Lorem ipsum dolor sit amet</p></div></div>
</section>

<section class="cats">
  <h2 class="section-title">Our Categories</h2>
  <svg class="arrow" style="left:50px" width="18" height="30" viewBox="0 0 18 30"><path d="M14 3L3 15l11 12" stroke="#666" stroke-width="3" fill="none"/></svg>
  <div class="cat-row">
    <div class="cat"><div class="tile" role="img" aria-label="Cat" style="background:#f9e79b"></div><span>Cat</span></div>
    <div class="cat"><div class="tile" role="img" aria-label="Dog" style="background:#a8d8e6"></div><span>Dog</span></div>
    <div class="cat"><div class="tile" role="img" aria-label="Rodent" style="background:#b5e39a"></div><span>Rodent</span></div>
    <div class="cat"><div class="tile" role="img" aria-label="Chicken" style="background:#e5e5e5"></div><span>Chicken</span></div>
    <div class="cat"><div class="tile" role="img" aria-label="Parrot" style="background:#f5bccb"></div><span>Birds</span></div>
  </div>
  <svg class="arrow" style="left:1134px" width="18" height="30" viewBox="0 0 18 30"><path d="M4 3l11 12L4 27" stroke="#666" stroke-width="3" fill="none"/></svg>
</section>

<section class="deals">
  <h2 class="section-title">This week's best deals</h2>
  <div class="deal-row">
    <div class="deal"><div style="position:absolute;inset:0;background:linear-gradient(135deg,#1a6fb8,#4aa7d6 60%,#0e4d7e)" role="img" aria-label="Tropical fish swimming in a blue aquarium"></div>
      <div class="shape"></div><div class="txt">Premium<br>Nutrition for<br>Every Aquarium<u>Shop Now</u></div></div>
    <div class="deal"><div style="position:absolute;inset:0;background:linear-gradient(135deg,#c2542a,#e9d8c8 60%,#f2ece4)" role="img" aria-label="Close-up of a chicken"></div>
      <div class="shape"></div><div class="txt" style="top:58px">Healthy<br>Feed for Happy<br>Chickens<u>Shop Now</u></div></div>
    <div class="deal"><div style="position:absolute;inset:0;background:linear-gradient(135deg,#9aa39a,#c9cfc4 55%,#e0c35a)" role="img" aria-label="Budgie on a colourful perch in a cage"></div>
      <div class="shape"></div><div class="txt" style="top:58px">Healthy<br>Feed for Happy<br>Chickens<u>Shop Now</u></div></div>
  </div>
</section>

<section class="featured">
  <h2 class="section-title">Featured Products</h2>
  <div class="prod-row">
    <div class="prod"><div class="img" role="img" aria-label="Small dog running through grass" style="background:linear-gradient(180deg,#a8c46a,#5e8a2a)"></div>
      <h5>10 Essential Pet Products Every New Owner Needs</h5><p>Pets become real family members who bring warmth and joy to their owners.</p><a>Read More</a></div>
    <div class="prod"><div class="img" role="img" aria-label="Kitten in a pink harness" style="background:linear-gradient(135deg,#8c8272,#d9c3c4 60%,#efc8d6)"></div>
      <h5>Excepteur sint occaecat cupidatat non proident, sunt in culpa</h5><p>Lorem ipsum dolor sit amet, consectetur adipiscing elit, sed do eiusmod tempor</p><a>Read More</a></div>
    <div class="prod"><div class="img" role="img" aria-label="Pile of dry feed pellets" style="background:radial-gradient(circle,#8a5a32,#5a3618)"></div>
      <h5>Duis aute irure dolor in reprehenderit</h5><p>Lorem ipsum dolor sit amet, consectetur adipiscing elit, sed do eiusmod tempor</p><a>Read More</a></div>
  </div>
</section>

<footer class="footer">
  <div class="brand"><span class="dot"></span>brenvik</div>
  <div class="fcol" style="left:432px"><h6>Quick Links</h6><ul>
    <li><svg width="12" height="12" viewBox="0 0 12 12"><path d="M1 6h8M6 2l4 4-4 4" stroke="#fff" stroke-width="2" fill="none"/></svg>Home</li>
    <li><svg width="12" height="12" viewBox="0 0 12 12"><path d="M1 6h8M6 2l4 4-4 4" stroke="#fff" stroke-width="2" fill="none"/></svg>About</li>
    <li><svg width="12" height="12" viewBox="0 0 12 12"><path d="M1 6h8M6 2l4 4-4 4" stroke="#fff" stroke-width="2" fill="none"/></svg>Chicken Food</li>
    <li><svg width="12" height="12" viewBox="0 0 12 12"><path d="M1 6h8M6 2l4 4-4 4" stroke="#fff" stroke-width="2" fill="none"/></svg>Accessories</li>
    <li><svg width="12" height="12" viewBox="0 0 12 12"><path d="M1 6h8M6 2l4 4-4 4" stroke="#fff" stroke-width="2" fill="none"/></svg>Contact Us</li></ul></div>
  <div class="fcol" style="left:664px"><h6>Help Links</h6><ul>
    <li><svg width="12" height="12" viewBox="0 0 12 12"><path d="M1 6h8M6 2l4 4-4 4" stroke="#fff" stroke-width="2" fill="none"/></svg>FAQ</li>
    <li><svg width="12" height="12" viewBox="0 0 12 12"><path d="M1 6h8M6 2l4 4-4 4" stroke="#fff" stroke-width="2" fill="none"/></svg>Terms of use</li>
    <li><svg width="12" height="12" viewBox="0 0 12 12"><path d="M1 6h8M6 2l4 4-4 4" stroke="#fff" stroke-width="2" fill="none"/></svg>Privacy Policy</li>
    <li><svg width="12" height="12" viewBox="0 0 12 12"><path d="M1 6h8M6 2l4 4-4 4" stroke="#fff" stroke-width="2" fill="none"/></svg>Support Links</li>
    <li><svg width="12" height="12" viewBox="0 0 12 12"><path d="M1 6h8M6 2l4 4-4 4" stroke="#fff" stroke-width="2" fill="none"/></svg>Conditions</li></ul></div>
  <div class="fcol" style="left:899px"><h6>Contact Us</h6>
    <div class="fcontact"><span class="ic"><svg width="14" height="18" viewBox="0 0 14 18"><path d="M7 0a7 7 0 017 7c0 5-7 11-7 11S0 12 0 7a7 7 0 017-7z" fill="#3c3c3b"/><circle cx="7" cy="7" r="2.5" fill="#fff"/></svg></span><span>Brenvik<br>Netherlands</span></div>
    <div class="fcontact"><span class="ic"><svg width="15" height="15" viewBox="0 0 24 24"><path d="M6.6 10.8a15 15 0 006.6 6.6l2.2-2.2a1 1 0 011-.25 11.4 11.4 0 003.6.57 1 1 0 011 1V20a1 1 0 01-1 1A17 17 0 013 4a1 1 0 011-1h3.5a1 1 0 011 1c0 1.25.2 2.45.57 3.6a1 1 0 01-.25 1z" fill="#3c3c3b"/></svg></span><span style="line-height:32px">+31 20 555 0147</span></div>
    <div class="fcontact"><span class="ic"><svg width="15" height="12" viewBox="0 0 18 14"><rect width="18" height="14" rx="2" fill="#3c3c3b"/><path d="M1 2l8 6 8-6" stroke="#fff" stroke-width="1.6" fill="none"/></svg></span><span style="line-height:32px">info@brenvik.nl</span></div>
  </div>
  <div class="rule"></div>
  <div class="copy">Copyrights@2025.Brenvik.nl All Rights Reserved</div>
</footer>

</body>
</html>
```